Social Media Cover and Profile

We already have our own logo. We just need a fresh design on our social media pages. We are not happy with our current designs. We would like to incorporate our ZING billboard and the colors are blue (#05143f) and white. You can also incorporate silver as well. We are a family law office (Divorce and Custody) We no longer want to incorporate the Capital of Harrisburg photo that we are currently using. You can look at our Facebook page; The Law Office of Milo T. Brennick.

Target Market(s)

Potential Clients

Industry/Entity Type

Family Law

Logo Text

Our Logo Is The Law Office of Milo T. Brennick with the Sheild

Requirements
Must have
• Text to include:
Central Pennslyvania's Premier Family Law Firm

Ability to be resized to and used as all images in social media, including but not limited to: Youtube Channel art, Facebook Cover and Profile.
Nice to have
• Darker color but we are open to "bright" ideas.

```html
<!DOCTYPE html>
<html lang="en">
<head>
<meta charset="utf-8">
<title>Milo T. Brennick – Social Cover</title>
<link href="https://fonts.googleapis.com/css2?family=Cinzel:wght@400;600&family=EB+Garamond:wght@500&display=swap" rel="stylesheet">
<style>
  :root {
    --stage: #1e1e1e;
    --navy: #05143f;
    --navy-mid: #0b2466;
    --navy-light: #1d3d8f;
    --white: #ffffff;
    --silver-light: #f4f5f7;
    --silver-mid: #b9bcc3;
    --silver-dark: #7d818a;
  }
  html, body {
    margin: 0;
    padding: 0;
    width: 1200px;
    height: 797px;
    overflow: hidden;
    background: var(--stage);
  }
  .cover {
    position: absolute;
    left: 50px;
    top: 198px;
    width: 1100px;
    height: 401px;
    overflow: hidden;
    background: linear-gradient(90deg, var(--navy-mid) 0%, var(--navy) 100%);
  }
  .cover__photo {
    position: absolute;
    left: 0;
    top: 0;
    width: 620px;
    height: 401px;
    background:
      linear-gradient(90deg, rgba(5,20,63,0) 60%, var(--navy-mid) 100%),
      radial-gradient(ellipse at 28% 30%, #2a5a5a 0%, var(--navy-light) 35%, var(--navy-mid) 75%);
    opacity: .9;
  }
  .brand {
    position: absolute;
    left: 56px;
    top: 46px;
    display: flex;
    align-items: center;
    gap: 10px;
    font-family: "Cinzel", serif;
    font-weight: 600;
    font-size: 17px;
    letter-spacing: .5px;
    color: var(--white);
  }
  .brand__mark {
    width: 40px;
    height: 40px;
    border-radius: 50%;
    background: var(--white);
  }
  .headline {
    position: absolute;
    left: 46px;
    top: 112px;
    margin: 0;
    font-family: "Cinzel", serif;
    font-weight: 600;
    font-size: 162px;
    line-height: 1;
    letter-spacing: 2px;
    background: linear-gradient(180deg, var(--silver-light) 0%, var(--silver-mid) 45%, var(--silver-dark) 60%, var(--silver-light) 100%);
    -webkit-background-clip: text;
    background-clip: text;
    color: transparent;
  }
  .divider {
    position: absolute;
    left: 563px;
    top: 112px;
    width: 1px;
    height: 221px;
    background: var(--silver-mid);
    opacity: .7;
  }
  .tagline {
    position: absolute;
    left: 640px;
    top: 110px;
    margin: 0;
    font-family: "Cinzel", serif;
    font-weight: 400;
    font-size: 46px;
    line-height: 55px;
    color: var(--white);
  }
  .web {
    position: absolute;
    left: 0;
    width: 1100px;
    top: 362px;
    text-align: center;
    font-family: "EB Garamond", serif;
    font-weight: 500;
    font-size: 21px;
    letter-spacing: 2px;
    color: var(--white);
  }
</style>
</head>
<body>
  <section class="cover">
    <div class="cover__photo" role="img" aria-label="Photo of a domed government building with columns, toned in deep blue"></div>
    <div class="brand"><span class="brand__mark"></span><span>The Law Office of Milo T. Brennick</span></div>
    <h1 class="headline">ZING</h1>
    <div class="divider"></div>
    <p class="tagline">Central<br>Pennslyvania's<br>Premier Family<br>Law Firm</p>
    <div class="web">www.MiloBrennickLaw.com</div>
  </section>
</body>
</html>
```